real esate business card with company logo and name

we need a business card design for a real esate company

The company name is Walsh & Brand Pty Ltd, and we have our logo designed and will upload. We want classic or moden feel. Black or white background. looks more textured. Should include folowinginformations
Owen Walsh and Lucy Brand
Sales Agents & Onsite Manager
p: 07 5948 2063
F: 07 5948 2174
M:0431 857 219
3/42 Marlow Crescent, FERNLEA QLD 4213

We want this business card looks professonal. Thank you in advance.

Industry/Entity Type

Real Estate Agent

Contact Information for Business Card

Owen Walsh and Lucy Brand
Onsite Manager & Sales Agents
p: 07 5948 2063
M:0431 857 219

Font styles to use
Serif

Colors
000000
fbfbfb
333333
959595

Requirements
Must have
• company logo and name, black or white back ground

```html
<!DOCTYPE html>
<html lang="en">
<head>
<meta charset="utf-8">
<title>Walsh &amp; Brand Pty Ltd — Business Card</title>
<link href="https://fonts.googleapis.com/css2?family=Source+Sans+3:wght@400;600&display=swap" rel="stylesheet">
<style>
  :root {
    --page-bg: #2e2e2e;
    --card-dark: #4a4a4a;
    --card-light: #f7f7f7;
    --ink-light: #fbfbfb;
    --ink-soft: #e6e6e6;
    --ink-dark: #5a5a5a;
    --accent-grey: #959595;
  }
  * { margin: 0; padding: 0; box-sizing: border-box; }
  html, body {
    width: 1200px; height: 750px; overflow: hidden;
    background: var(--page-bg);
    font-family: "Source Sans 3", sans-serif;
  }
  .stage { position: relative; width: 1200px; height: 750px; }

  .card {
    position: absolute; top: 228px;
    width: 462px; height: 262px;
    background: var(--card-dark);
    overflow: hidden;
  }
  .card-front { left: 124px; }
  .card-back { left: 618px; }

  /* front: light brand panel */
  .brand-panel {
    position: absolute; left: 0; top: 0;
    width: 222px; height: 100%;
    background: var(--card-light);
  }
  .brand-lockup {
    position: absolute; left: 0; top: 96px; width: 222px;
    display: flex; flex-direction: column; align-items: center; gap: 10px;
  }
  .brand-square {
    width: 56px; height: 56px; background: var(--ink-dark);
  }
  .brand-name {
    font-size: 10.5px; font-weight: 600; letter-spacing: 0.6px;
    color: var(--ink-dark); text-transform: uppercase;
  }

  .divider {
    position: absolute; left: 222px; top: 0; height: 100%; width: 14px;
  }

  .details {
    position: absolute; left: 255px; top: 68px;
    color: var(--ink-light);
  }
  .agent-names { font-size: 16.5px; font-weight: 600; line-height: 1.1; }
  .agent-role { font-size: 12px; color: var(--ink-soft); margin-top: 3px; }
  .address { font-size: 10.5px; line-height: 14px; margin-top: 12px; color: var(--ink-soft); }
  .contact-list { list-style: none; margin-top: 10px; }
  .contact-list li {
    display: flex; align-items: center; gap: 7px;
    font-size: 10.5px; height: 17.7px; color: var(--ink-soft);
  }
  .contact-list svg { width: 11px; height: 11px; flex: none; }

  /* back */
  .back-lockup {
    position: absolute; right: 28px; bottom: 27px;
    display: flex; flex-direction: column; align-items: center; gap: 10px;
  }
  .back-lockup .brand-square { width: 62px; height: 62px; background: var(--ink-light); }
  .back-name { font-size: 11px; font-weight: 600; letter-spacing: 0.6px; color: var(--ink-light); text-transform: uppercase; }
  .back-url { font-size: 10px; letter-spacing: 1.6px; color: var(--ink-soft); }
</style>
</head>
<body>
<main class="stage">

  <section class="card card-front">
    <div class="brand-panel">
      <div class="brand-lockup">
        <div class="brand-square"></div>
        <div class="brand-name">Walsh &amp; Brand Pty Ltd</div>
      </div>
    </div>

    <svg class="divider" viewBox="0 0 14 262" aria-hidden="true">
      <rect x="2" y="0" width="4" height="262" fill="#dcdcdc"/>
      <path d="M4 70 L10 86 L4 102 L-2 86 Z" fill="#f7f7f7" stroke="#4a4a4a" stroke-width="1.2"/>
    </svg>

    <div class="details">
      <h1 class="agent-names">Owen Walsh &amp; Lucy Brand</h1>
      <p class="agent-role">Sales Agents &amp; Onsite Manager</p>
      <p class="address">3/42 Marlow Crescent<br>FERNLEA QLD 4213</p>
      <ul class="contact-list">
        <li>
          <svg viewBox="0 0 12 12"><path d="M2.2 1 L4.2 1 L5 3.4 L3.8 4.4 Q4.8 6.8 7.4 8.2 L8.4 7 L11 7.8 L11 9.8 Q10.6 11 9 11 Q1 10 1 2.6 Q1 1.2 2.2 1 Z" fill="#fbfbfb"/></svg>
          07 5948 2063
        </li>
        <li>
          <svg viewBox="0 0 12 12"><rect x="3" y="0.5" width="6" height="11" rx="1" fill="none" stroke="#fbfbfb" stroke-width="1.2"/><rect x="5" y="9" width="2" height="1" fill="#fbfbfb"/></svg>
          0431 857 219
        </li>
        <li>
          <svg viewBox="0 0 12 12"><rect x="3" y="1" width="6" height="3" fill="#fbfbfb"/><rect x="0.5" y="4.5" width="11" height="5" rx="1" fill="#fbfbfb"/><rect x="3" y="8" width="6" height="3" fill="#ddd"/></svg>
          07 5948 2174
        </li>
        <li>
          <svg viewBox="0 0 12 12"><circle cx="6" cy="6" r="5.2" fill="none" stroke="#fbfbfb" stroke-width="1.2"/><path d="M1 6 H11 M6 1 Q3 6 6 11 M6 1 Q9 6 6 11" fill="none" stroke="#fbfbfb" stroke-width="0.9"/></svg>
          www.walshbrand.com
        </li>
      </ul>
    </div>
  </section>

  <section class="card card-back">
    <div class="back-lockup">
      <div class="brand-square"></div>
      <div class="back-name">Walsh &amp; Brand</div>
      <div class="back-url">www.walshbrand.com</div>
    </div>
  </section>

</main>
</body>
</html>
```